Web Design Project

Psychotherapy and Counselling Practice needs a landing page web design.

My business "Larkfield Advisory" specialises in the treatment of Anxiety and Depression with a holistic approach, endeavouring to unlock the key that holds us to ransom in a life that is imbalanced, frustrating, and ultimately of our own making due to our own perceptions and behaviours.

There is much that impacts us which we cannot change, but we are always in control of how we think, and how we frame our experiences.....learning to challenge those thoughts and behaviours that are destructive and disempowering opens up a world of joyful possibility. Life is about making choices, learn to make wiser and healthier choices.......

Larkfield Advisory has a client base of individual clients but will seek to expand to offer services to the Corporate world by offering an adjunct to employers for established "Wellness Programs".

Larkfield Advisory is a highly professional, ethically bound business, with the needs of the client at the forefront of all we do.

Larkfield Advisory wishes to avoid the usual "jargon driven" psychobabble offered on many counselling web pages. It aims to be stylishly presented, clean in look and with as few "words" as possible and a largely white background (faster loading and more powerful impact of what is stated), those words contained in the webpage should be meaningful, persuasive and have an impact simply at glance. Larkfield does not want , or expect, those prospective clients in need of support , to be reading through volumes of industry driven cliches.

At this point Larkfield is just looking for a high quality landing page. However in time this will likely expand to include other sections such as case studies, video content etc.

Target Market(s)

Those in need of emotional support, suffering mental health issues, and those simply wanting to become self aware supported by a mindful therapist.

Industry/Entity Type

Industry

Requirements
Must have
• The design must incorporate the Larkfield logo and colour schemes found on the attached files.

```html
<!DOCTYPE html>
<html lang="en">
<head>
<meta charset="utf-8">
<title>Larkfield Advisory</title>
<link rel="stylesheet" href="https://fonts.googleapis.com/css2?family=Arimo:ital,wght@0,400;0,700;1,400&display=swap">
<style>
:root{
  --green:#7f9f00;
  --green-dark:#6a8600;
  --green-light:#8fb20e;
  --text:#666;
  --dark:#222;
  --panel:#f0f0f0;
  --white:#fff;
  --grey-top:#9a9a9a;
  --grey-bottom:#6e6e6e;
}
*{box-sizing:border-box;margin:0;padding:0}
html,body{width:1156px;height:1200px;overflow:hidden}
body{font-family:"Arimo",Arial,sans-serif;background:linear-gradient(var(--grey-top) 180px,#8a8a8a 600px,var(--grey-bottom) 1200px);position:relative;color:var(--text)}
a{color:inherit;text-decoration:none}
.site-header{position:absolute;left:0;top:0;width:1156px;height:184px;background:var(--white);border-bottom:5px solid var(--green)}
.brand{position:absolute;left:82px;top:6px;width:190px;height:172px;display:flex;align-items:center;justify-content:center;gap:8px}
.brand-mark{width:10px;height:10px;background:var(--green)}
.brand-name{font-size:26px;color:var(--green);letter-spacing:1px}
.profile{position:absolute;left:720px;top:18px}
.profile-photo{position:absolute;left:0;top:0;width:92px;height:96px;border:4px solid #e6e6e6;border-radius:3px;background:linear-gradient(#cfd6dc,#7d8690)}
.profile-name{position:absolute;left:106px;top:0;font-size:22px;color:#777;white-space:nowrap}
.profile-quals{position:absolute;left:106px;top:26px;font-size:14px;color:#777;white-space:nowrap}
.profile-phone{position:absolute;left:106px;top:55px;font-size:14px;color:var(--green);white-space:nowrap}
.profile-mail{position:absolute;left:106px;top:79px;font-size:14px;color:var(--green);white-space:nowrap}
.profile-mail span{font-size:16px}
.main-nav{position:absolute;left:512px;top:136px;height:44px;display:flex;background:linear-gradient(#8cb00a,var(--green-dark));border-radius:3px 3px 0 0}
.main-nav a{color:var(--white);font-size:14px;line-height:44px;padding:0 18px;border-right:1px solid #5d7600}
.main-nav a:first-child{padding-left:23px}
.main-nav a:last-child{border-right:0;padding-right:22px}
.page{position:absolute;left:86px;top:184px;width:979px;height:913px;background:var(--white)}
.hero{position:absolute;left:6px;top:8px;width:966px;height:323px;border-radius:4px;background:#121212;overflow:hidden}
.hero-photo{position:absolute;left:0;top:0;width:560px;height:323px;background:radial-gradient(ellipse at 50% 45%,#c86fb0 0%,#8a3f7a 30%,#2a3a1c 60%,#121212 85%)}
.hero-title{position:absolute;left:616px;top:92px;font-size:24px;font-weight:700;color:var(--green-light)}
.hero-sub{position:absolute;left:616px;top:124px;font-size:22px;font-weight:700;color:var(--white)}
.hero-btn{position:absolute;left:616px;top:164px;width:150px;height:37px;border-radius:3px;background:linear-gradient(#9a9a9a,#6a6a6a);color:var(--white);font-weight:700;font-size:15px;line-height:37px;padding-left:13px}
.hero-btn svg{position:absolute;right:11px;top:9px}
.hero-dots{position:absolute;left:829px;top:279px;display:flex;gap:11px}
.hero-dots i{width:20px;height:20px;border-radius:50%;border:3px solid #ddd;background:#777}
.hero-dots i.on{background:var(--green)}
.hero-shadow{position:absolute;left:10px;top:336px;width:960px;height:22px;background:radial-gradient(ellipse at 50% 0,rgba(0,0,0,.14),transparent 70%)}
h2{font-size:19px;font-weight:700;color:var(--green)}
.welcome h2{position:absolute;left:15px;top:376px}
.welcome p{position:absolute;left:15px;top:409px;width:654px;font-size:13px;line-height:22px;text-align:justify}
.divider{position:absolute;left:12px;top:536px;width:658px;border-top:1px solid #e3e3e3}
.research h2{position:absolute;left:14px;top:550px}
.cards{position:absolute;left:16px;top:588px;display:flex;gap:27px}
.card{width:199px;height:229px;background:var(--panel);border-radius:3px;padding:6px}
.card-photo{height:118px;border-radius:3px}
.card p{font-size:13px;line-height:20px;padding:10px 10px 0;color:#777}
.card a{display:block;font-size:11px;font-weight:700;color:var(--dark);padding:6px 11px}
.card a b{margin-left:6px}
.newsletter{position:absolute;left:16px;top:831px;width:652px;height:64px;border-radius:3px;background:linear-gradient(#6f6f6f,#3c3c3c)}
.newsletter svg{position:absolute;left:28px;top:18px}
.newsletter h3{position:absolute;left:82px;top:21px;font-size:20px;font-weight:700;color:var(--white)}
.newsletter-form{position:absolute;left:305px;top:11px;width:320px;height:41px;background:var(--white);border-radius:3px;border:1px solid #ccc}
.newsletter-form span{position:absolute;left:15px;top:11px;font-size:14px;color:#888}
.newsletter-form b{position:absolute;right:3px;top:3px;width:96px;height:33px;background:linear-gradient(#555,#222);border-radius:2px;color:var(--white);font-size:15px;line-height:33px;text-align:center}
.side h2{position:absolute;left:693px}
.more{position:absolute;left:932px;width:18px;height:18px;border-radius:50%;background:#bbb}
.more svg{position:absolute;left:5px;top:4px}
.news-item{position:absolute;left:691px;width:275px;height:117px;background:var(--panel);border-radius:3px;padding:12px 16px}
.news-item p{font-size:13px;line-height:22px;color:#777;text-align:justify}
.news-item time{display:block;font-size:13px;color:var(--dark);margin-top:4px}
.quote{position:absolute;left:691px;top:725px;width:275px;height:171px;background:var(--panel);border-radius:3px;padding:16px 16px}
.quote p{font-size:13px;line-height:22px;font-style:italic;color:#777;text-align:justify}
.quote cite{display:block;font-style:normal;font-size:13px;color:var(--dark);margin-top:6px}
.site-footer nav{position:absolute;left:86px;top:1119px;font-size:14px;color:var(--white)}
.site-footer nav span{margin:0 9px}
.copyright{position:absolute;left:86px;top:1151px;font-size:14px;color:var(--white)}
.social{position:absolute;left:1011px;top:1133px;display:flex;gap:6px}
.social i{width:24px;height:24px;border-radius:3px;background:#3b5d9c}
.social i+i{background:#4fb8e6}
</style>
</head>
<body>
<header class="site-header">
  <div class="brand"><span class="brand-mark"></span><span class="brand-name">LARKFIELD</span></div>
  <div class="profile">
    <div class="profile-photo" role="img" aria-label="Portrait photograph of the therapist"></div>
    <div class="profile-name">Morgan Hale BA</div>
    <div class="profile-quals">(Psych) BSc (Hons) Psych MBPS</div>
    <div class="profile-phone">Mobile : 0400 123 456</div>
    <div class="profile-mail">E-mail : <span>morgan.hale@examplemail.com</span></div>
  </div>
  <nav class="main-nav">
    <a href="#">Home</a><a href="#">About us</a><a href="#">Services</a><a href="#">Programs</a><a href="#">Seminars</a><a href="#">Contact us</a>
  </nav>
</header>

<main class="page">
  <section class="hero">
    <div class="hero-photo" role="img" aria-label="Close-up photograph of a pink orchid flower on a dark background"></div>
    <div class="hero-title">ANXIETY AND DEPRESSION</div>
    <div class="hero-sub">Approach consulting</div>
    <a class="hero-btn" href="#">CONTACT US<svg width="18" height="18" viewBox="0 0 18 18"><circle cx="9" cy="9" r="9" fill="#555"/><path d="M7.5 5.5l3.5 3.5-3.5 3.5" stroke="#fff" stroke-width="2" fill="none"/></svg></a>
    <div class="hero-dots"><i class="on"></i><i></i><i></i><i></i></div>
  </section>
  <div class="hero-shadow"></div>

  <section class="welcome">
    <h2>Welcome to Larkfield</h2>
    <p>Cras vestibulum a massa at pharetra. Nunc sed lacinia velit, eu commodo elit. Maecenas porta nec velit in pharetra. Cras tortor neque, pretium ut nibh a, facilisis iaculis arcu. Interdum et malesuada fames ac ante ipsum primis in faucibus. Curabitur gravida metus ut urna dapibus vulputate eget sed sem. Aenean tincidunt, tortor at tris tique condimentum, felis neque mollis massa, quis interdum eros leo ac est. Donec sit amet odio eget nibh convallis ultricies. Cum sociis natoque penatibus et magnis dis parturient montes,c</p>
  </section>
  <div class="divider"></div>

  <section class="research">
    <h2>Our Research</h2>
    <div class="cards">
      <article class="card">
        <div class="card-photo" role="img" aria-label="Photograph of a garden chair on a lawn overlooking the sea" style="background:linear-gradient(#8ab4dc 0%,#cfe0ee 35%,#6f8a3a 45%,#4e6a2a 100%)"></div>
        <p>Aliquam mi eleifend consect etur, libero velit congue nibh, et porttitor sapien.</p>
        <a href="#">VIEW MORE<b>»</b></a>
      </article>
      <article class="card">
        <div class="card-photo" role="img" aria-label="Photograph of a waterfall over mossy rocks" style="background:linear-gradient(160deg,#2a2a22,#4f7a2a 45%,#b7c6c8 70%,#3a3a30)"></div>
        <p>Aliquam mi eleifend consect etur, libero velit congue nibh, et porttitor sapien.</p>
        <a href="#">VIEW MORE<b>»</b></a>
      </article>
      <article class="card">
        <div class="card-photo" role="img" aria-label="Photograph of a lone tree at sunset" style="background:linear-gradient(#3a2a1e,#c9701e 45%,#f0b04a 60%,#6a3a1a)"></div>
        <p>Aliquam mi eleifend consect etur, libero velit congue nibh, et porttitor sapien.</p>
        <a href="#">VIEW MORE<b>»</b></a>
      </article>
    </div>
  </section>

  <section class="newsletter">
    <svg width="42" height="28" viewBox="0 0 42 28"><rect x="1" y="1" width="40" height="26" fill="#f2f2f2" stroke="#ccc"/><path d="M1 1l20 15 20-15M1 27l15-13M41 27l-15-13" stroke="#bbb" fill="none"/></svg>
    <h3>Newsletter Subscribe</h3>
    <div class="newsletter-form"><span>Enter your mail ID</span><b>Subscribe</b></div>
  </section>

  <aside class="side">
    <h2 style="top:376px">Latest News &amp; Events</h2>
    <span class="more" style="top:375px"><svg width="8" height="10" viewBox="0 0 8 10"><path d="M2 1l4 4-4 4" stroke="#fff" stroke-width="2" fill="none"/></svg></span>
    <div class="news-item" style="top:414px">
      <p>Tnascetur ridiculus mus. Aenean pharetra neque vel est hendrerit dapibus. Morbi dapibus metus ac nisi ultricies.</p>
      <time>Jun-12-2013</time>
    </div>
    <div class="news-item" style="top:538px">
      <p>Tnascetur ridiculus mus. Aenean pharetra neque vel est hendrerit dapibus. Morbi dapibus metus ac nisi ultricies.</p>
      <time>Jun-12-2013</time>
    </div>
    <h2 style="top:687px">Client’s Testimonials</h2>
    <span class="more" style="top:686px"><svg width="8" height="10" viewBox="0 0 8 10"><path d="M2 1l4 4-4 4" stroke="#fff" stroke-width="2" fill="none"/></svg></span>
    <blockquote class="quote">
      <p><b style="font-size:20px;color:#555;font-style:normal">“</b> Phasellus et magna id ante egestas henlibero, a sagittis lorem porta vitae. Quisque dapibus turpis fringilla, eget commodo felis interdum. Sed blandit felis ipsum, sed quam orci, et cursus <b style="font-size:20px;color:#555;font-style:normal">”</b></p>
      <cite>Client name, City</cite>
    </blockquote>
  </aside>
</main>

<footer class="site-footer">
  <nav><a href="#">Home</a><span>|</span><a href="#">About us</a><span>|</span><a href="#">Services</a><span>|</span><a href="#">Programs</a><span>|</span><a href="#">Seminars</a><span>|</span><a href="#">Contact us</a></nav>
  <div class="copyright">Copyright &copy; 2013 &nbsp;&nbsp; www.larkfieldadvisory.com.au &nbsp;&nbsp; All rights reserved.</div>
  <div class="social"><i></i><i></i></div>
</footer>
</body>
</html>
```